Boutique Store Selling Antiques and Unique Finds

I need a Web Page designed for my Store Called "Willow Lane". I would like a very classic, muted design that looks European when pulled up. I will be selling Antiques from all over the world and Unique finds that have reproduced. I will also be selling high-end purses and jewelry with unique, reasonable products for the every-day buyer as well.

Target Market(s)

25-70 year old men and women;)

Coding

Coded - Design and coding required

Number of Pages Required

1 page

Colors

Designer to choose only greyscale colors for use in the design.

Requirements
Must have
• I want it

```html
<!DOCTYPE html>
<html lang="en">
<head>
<meta charset="utf-8">
<title>Willow Lane — Antiques &amp; Unique Finds</title>
<link rel="stylesheet" href="https://fonts.googleapis.com/css2?family=Roboto+Slab:wght@300;400&family=Lato:wght@400;700&family=Crimson+Text:ital@1&family=Cinzel:wght@400&display=swap">
<style>
:root{
  --accent:#7d7d7d;
  --accent-strong:#8e8e8e;
  --accent-light:#d2d2d2;
  --ink:#3a3a3a;
  --muted:#6a6a6a;
  --rule:#b9b9b9;
  --white:#ffffff;
  --footer:#2f2f2f;
  --footer-text:#d8d8d8;
}
*{margin:0;padding:0;box-sizing:border-box}
html,body{width:1200px;height:3128px;overflow:hidden}
body{position:relative;font-family:"Lato",sans-serif;color:var(--ink);background:#7f7f7f}
.abs{position:absolute}
.backdrop{left:0;top:0;width:1200px;height:2794px;background:linear-gradient(180deg,#666 0%,#9e9e9e 20%,#8a8a8a 50%,#6e6e6e 80%,#4e4e4e 100%)}
.logo{left:119px;top:104px;font-family:"Cinzel",serif;font-size:27px;letter-spacing:3px;color:var(--white);display:flex;align-items:center;gap:10px}
.logo .dot{width:10px;height:10px;border-radius:50%;background:var(--white)}
.nav a{position:absolute;top:113px;height:30px;line-height:30px;font-family:"Roboto Slab",serif;font-size:12px;color:var(--white);text-decoration:none;letter-spacing:.5px}
.nav .active{left:428px;width:61px;text-align:center;background:var(--accent-strong)}
.panel{left:120px;top:239px;width:966px;height:2479px;background:var(--white)}
.hero{left:128px;top:247px;width:951px;height:441px;background:linear-gradient(180deg,#5e5e5e 0%,#b5b5b5 18%,#dadada 45%,#a8a8a8 70%,#3a3a3a 100%)}
.hero-card{left:577px;top:468px;width:412px;height:180px;background:rgba(72,72,72,.88);border:1px solid #bdbdbd;padding:34px 18px 0}
.hero-card h2{font-family:"Roboto Slab",serif;font-weight:300;font-size:28px;color:var(--white);letter-spacing:.5px;white-space:nowrap}
.hero-card h2 span{color:var(--accent-light)}
.hero-card p{font-size:12.5px;line-height:22px;color:#eee;margin-top:6px}
.hero-card .more{display:block;margin-top:10px;font-family:"Crimson Text",serif;font-style:italic;font-size:12px;color:var(--white)}
.eyebrow{font-family:"Crimson Text",serif;font-style:italic;color:var(--accent);text-align:center}
.title{font-family:"Roboto Slab",serif;font-weight:300;text-align:center;letter-spacing:2px}
.rule{height:1px;background:var(--rule)}
.lead{left:380px;top:852px;width:446px;text-align:center;font-size:15px;line-height:24px;color:var(--muted)}
.card{width:264px}
.card .photo{width:264px;height:264px}
.card .label{position:absolute;left:0;top:201px;width:233px;height:63px;background:var(--white);padding:16px 0 0 11px}
.card .label em{display:block;font-family:"Crimson Text",serif;font-size:14px;color:var(--accent)}
.card .label b{display:block;font-family:"Roboto Slab",serif;font-weight:300;font-size:18px;color:var(--ink);margin-top:1px;white-space:nowrap}
.card .price{position:absolute;left:12px;top:290px;font-weight:700;font-size:15px;color:var(--accent)}
.card .buy{position:absolute;left:0;top:338px;display:flex;align-items:center;gap:10px;font-family:"Roboto Slab",serif;font-size:11px;color:var(--ink)}
.card .buy i{display:block;width:31px;height:1px;background:var(--accent)}
.load{left:532px;top:1775px;width:137px;height:45px;border:1px solid var(--accent);text-align:center;line-height:45px;font-family:"Roboto Slab",serif;font-size:12px;letter-spacing:1px;color:var(--ink)}
.sale{left:120px;top:1923px;width:966px;height:376px;background:linear-gradient(110deg,#363636 0%,#646464 40%,#424242 70%,#5c5c5c 100%)}
.sale-text{left:120px;width:966px;text-align:center;color:var(--white)}
.shop{left:561px;top:2175px;width:111px;height:40px;border:1px solid var(--accent-light);line-height:38px;text-align:center;font-size:11px;font-weight:700;color:var(--white)}
.promo{top:2379px;width:404px;height:260px}
.promo-label{top:2484px;width:237px;height:51px;background:var(--white);text-align:center;line-height:51px;font-family:"Roboto Slab",serif;font-weight:300;font-size:20px;color:var(--muted);letter-spacing:.5px}
.footer{left:0;top:2794px;width:1200px;height:334px;background:var(--footer)}
.footer-logo{left:0;top:2868px;width:1200px;text-align:center;font-family:"Cinzel",serif;font-size:30px;letter-spacing:4px;color:#bdbdbd}
.fcol{font-family:"Roboto Slab",serif;font-size:12px;color:var(--footer-text);letter-spacing:.5px}
.fcol li{list-style:none}
.social{left:866px;top:2976px;display:flex;gap:8px}
.social i{display:block;width:28px;height:28px;border:1px solid #bbb;border-radius:50%}
.top-btn{left:1142px;top:3067px;width:39px;height:39px;background:#474747}
</style>
</head>
<body>
<div class="abs backdrop" role="img" aria-label="Bright gallery hall with arched windows and marble floor"></div>

<header>
  <div class="abs logo"><span class="dot"></span>Willow Lane</div>
  <nav class="nav">
    <a class="active" href="#">HOME</a>
    <a style="left:533px" href="#">COLLECTION</a>
    <a style="left:669px" href="#">OTHERS</a>
    <a style="left:770px" href="#">SALE</a>
  </nav>
  <svg class="abs" style="left:975px;top:119px" width="20" height="18" viewBox="0 0 20 18" fill="none" stroke="#fff" stroke-width="1.2"><rect x="1" y="5" width="12" height="12"/><path d="M4 5V3a3 3 0 0 1 6 0v2"/><text x="15" y="5" font-size="6" fill="#fff" stroke="none">0</text></svg>
  <svg class="abs" style="left:1017px;top:121px" width="16" height="16" viewBox="0 0 16 16" fill="none" stroke="#fff" stroke-width="1.3"><circle cx="6.5" cy="6.5" r="5"/><path d="M10.5 10.5L15 15"/></svg>
  <svg class="abs" style="left:1058px;top:123px" width="22" height="10" viewBox="0 0 22 10" stroke="#fff" stroke-width="1.2"><path d="M0 1h22M0 9h22"/></svg>
</header>

<main>
  <div class="abs panel"></div>

  <section>
    <div class="abs hero" role="img" aria-label="Antique crown with stones on a stone pedestal under an ornate frame"></div>
    <div class="abs hero-card">
      <h2><span>ANTIQUE</span> FRENCH CROWN</h2>
      <p>Lorem ipsum dolor sit amet, consectetur ense adipisicing elit, sed do eiusmod inas alis dene tempor ins aliqua ut enim...</p>
      <span class="more">Know More..</span>
    </div>
  </section>

  <section>
    <div class="abs eyebrow" style="left:120px;top:774px;width:966px;font-size:18px">Our Latest Collection</div>
    <div class="abs rule" style="left:259px;top:822px;width:87px"></div>
    <h1 class="abs title" style="left:120px;top:796px;width:966px;font-size:44px;color:var(--ink)">NEW ARRIVALS</h1>
    <div class="abs rule" style="left:860px;top:822px;width:87px"></div>
    <p class="abs lead">Lorem ipsum dolor sit amet, consectetur adipisicing elit, sed do eiusmod tempor incididunt ut labore et</p>

    <article class="abs card" style="left:181px;top:957px">
      <div class="photo" role="img" aria-label="Wood panelled hall with crystal chandelier and statue" style="background:linear-gradient(160deg,#cfcfcf,#4a4a4a 45%,#262626)"></div>
      <div class="label"><em>Collection</em><b>ANTIQUE &amp; VINTAGE</b></div>
      <span class="price">$800.00</span>
      <span class="buy"><i></i>Buy Now</span>
    </article>
    <article class="abs card" style="left:471px;top:957px">
      <div class="photo" role="img" aria-label="Ornate frame, potted plant and vintage leather cases" style="background:linear-gradient(180deg,#5a5a5a,#b4b4b4 40%,#4a4a4a 70%,#333)"></div>
      <div class="label"><em>Collection</em><b>FURNISHING</b></div>
      <span class="price">$1000.00</span>
      <span class="buy"><i></i>Buy Now</span>
    </article>
    <article class="abs card" style="left:760px;top:957px">
      <div class="photo" role="img" aria-label="Jewelled crown against damask wall" style="background:linear-gradient(180deg,#d4d4d4,#707070 50%,#2a2a2a)"></div>
      <div class="label"><em>Collection</em><b>JEWELLERY</b></div>
      <span class="price">$1000.00</span>
      <span class="buy"><i></i>Buy Now</span>
    </article>

    <article class="abs card" style="left:181px;top:1364px">
      <div class="photo" role="img" aria-label="Fur hat with jewelled band" style="background:linear-gradient(180deg,#b8b8b8,#d6d6d6 45%,#222 75%,#555)"></div>
      <div class="label" style="top:199px"><em>Collection</em><b>ANTIQUE &amp; VINTAGE</b></div>
      <span class="price">$800.00</span>
      <span class="buy"><i></i>Buy Now</span>
    </article>
    <article class="abs card" style="left:471px;top:1364px">
      <div class="photo" role="img" aria-label="Embroidered thread insignia patch on black" style="background:radial-gradient(circle at 50% 55%,#6e6e6e,#262626 60%,#c4c4c4)"></div>
      <div class="label" style="top:199px"><em>Collection</em><b>ANTIQUE &amp; VINTAGE</b></div>
      <span class="price">$800.00</span>
      <span class="buy"><i></i>Buy Now</span>
    </article>
    <article class="abs card" style="left:760px;top:1364px">
      <div class="photo" role="img" aria-label="Ornate picture frames on patterned wall" style="background:linear-gradient(90deg,#3a3a3a,#8a8a8a 35%,#d0d0d0 60%,#6a6a6a)"></div>
      <div class="label" style="top:199px"><em>Collection</em><b>ANTIQUE &amp; VINTAGE</b></div>
      <span class="price">$800.00</span>
      <span class="buy"><i></i>Buy Now</span>
    </article>

    <div class="abs load">Load more</div>
  </section>

  <section>
    <div class="abs sale" role="img" aria-label="Shelves of fabric rolls, ribbons and textiles"></div>
    <div class="abs eyebrow" style="left:120px;top:2020px;width:966px;font-size:24px;color:var(--accent-light)">Willow Lane</div>
    <h2 class="abs title sale-text" style="top:2050px;font-size:44px;letter-spacing:1px">COLLECTION SALE</h2>
    <p class="abs sale-text" style="top:2108px;left:420px;width:366px;font-size:12.5px;line-height:22px">Lorem ipsum dolor sit amet, consectetur adipisicing elit, sed do eius mod tempor incididunt ut labore et dolore magna aliqua.</p>
    <div class="abs shop">SHOP NOW</div>
  </section>

  <section>
    <div class="abs promo" style="left:182px;background:linear-gradient(160deg,#cacaca,#444 45%,#b4b4b4)" role="img" aria-label="Green plant in a mercury glass vase"></div>
    <div class="abs promo-label" style="left:265px">COLLECTION SALE</div>
    <div class="abs promo" style="left:621px;background:linear-gradient(180deg,#bdbdbd,#858585 40%,#2a2a2a 65%,#5e5e5e 80%,#d2d2d2)" role="img" aria-label="Metal helmet resting on a stack of art books"></div>
    <div class="abs promo-label" style="left:708px">COLLECTION SALE</div>
  </section>
</main>

<footer>
  <div class="abs footer"></div>
  <div class="abs footer-logo">Willow Lane</div>
  <ul class="abs fcol" style="left:118px;top:2947px;line-height:31.7px">
    <li>48 Harrow Court Ellsworth</li>
    <li>555-014-2271, 555-019-3384</li>
    <li>enquiry@willowlane-shop.com</li>
    <li>Copyright © Larkfield Studio 2019</li>
  </ul>
  <ul class="abs fcol" style="left:435px;top:2946px;line-height:26.4px;font-size:11.5px">
    <li>Antique &amp; Vintage</li><li>Jewellery</li><li>Art</li><li>Furnishing</li><li>Others</li>
  </ul>
  <ul class="abs fcol" style="left:638px;top:2946px;line-height:26.4px;font-size:11.5px">
    <li>Terms &amp; Conditions</li><li>Privacy Policy</li><li>Refund Policy</li><li>My Account</li>
  </ul>
  <div class="abs fcol" style="left:866px;top:2946px;font-size:12.5px;color:#eee">Follow Us At:</div>
  <div class="abs social"><i></i><i></i><i></i><i></i><i></i></div>
  <div class="abs top-btn">
    <svg width="39" height="39" viewBox="0 0 39 39" fill="none" stroke="#ccc" stroke-width="1.2"><path d="M13 23l6.5-6.5L26 23"/></svg>
  </div>
</footer>
</body>
</html>
```